Hvac and insulation company needs good looking business card design

We are hvac and insulation company and looking for a new business cards that look to today standards designs

Target Market(s)

homeowners

Industry/Entity Type

Hvac

Contact Information for Business Card

Name: Walter Brinoku
Home comfort consultant
address: 4827 Dunmore St #215 Oakland, CA 94619
office: 888-316-2790
cell: 510-742-3185
Lic.# 584261
Email: walter@corvane-hvac.com
Web: corvane-hvac.com

Requirements
Must have
• clean and sleek look
Nice to have
• simple with a clean look
Should not have
• to busy business card

```html
<!DOCTYPE html>
<html lang="en">
<head>
<meta charset="utf-8">
<title>Corvane Business Card</title>
<link href="https://fonts.googleapis.com/css2?family=Lato:wght@400;700&display=swap" rel="stylesheet">
<style>
  :root {
    --backdrop: #e9ecf0;
    --card: #ffffff;
    --orange: #f58220;
    --ink: #6d6e70;
    --ink-soft: #808285;
    --band: #8a8b8d;
    --rule: #9d9ea0;
  }
  * { margin: 0; padding: 0; box-sizing: border-box; }
  html, body {
    width: 1200px;
    height: 1000px;
    overflow: hidden;
    background: var(--backdrop);
    font-family: "Lato", sans-serif;
  }
  .canvas { position: relative; width: 1200px; height: 1000px; }
  .card {
    position: absolute;
    left: 280px;
    width: 640px;
    height: 366px;
    background: var(--card);
    overflow: hidden;
  }
  .card--front { top: 100px; }
  .card--back { top: 534px; }

  .front-panel { position: absolute; inset: 0; }
  .brand-name {
    position: absolute;
    color: var(--orange);
    font-weight: 700;
    line-height: 1;
    letter-spacing: 0.5px;
  }
  .card--front .brand-name { right: 34px; top: 156px; font-size: 44px; }
  .card--back .brand-name { right: 30px; top: 42px; font-size: 46px; }
  .website {
    position: absolute;
    right: 38px;
    top: 308px;
    font-size: 19px;
    color: var(--ink);
  }

  .person { position: absolute; left: 33px; top: 102px; color: var(--ink); }
  .person-name { font-size: 35px; line-height: 1.1; }
  .person-title { font-size: 19px; line-height: 1.3; }
  .rule {
    position: absolute;
    left: 30px; right: 0; top: 178px;
    height: 2px;
    background: var(--rule);
  }
  .address-band { position: absolute; left: 192px; top: 178px; width: 448px; height: 32px; }
  .address-text {
    position: absolute;
    right: 30px; top: 184px;
    font-size: 17px;
    color: #ffffff;
    letter-spacing: 0.2px;
  }
  .contacts { position: absolute; left: 33px; top: 230px; list-style: none; }
  .contact {
    display: flex;
    align-items: center;
    gap: 14px;
    font-size: 22px;
    color: var(--ink);
    height: 32px;
  }
  .contact svg { width: 20px; height: 20px; fill: var(--ink-soft); flex: none; }
  .license {
    position: absolute;
    right: 28px; top: 316px;
    font-size: 17px;
    color: var(--ink);
  }
</style>
</head>
<body>
<main class="canvas">

  <section class="card card--front" aria-label="Card front">
    <svg class="front-panel" viewBox="0 0 640 366" aria-hidden="true">
      <polygon points="0,0 398,0 230,183 390,366 0,366" fill="var(--orange)"/>
    </svg>
    <div class="brand-name">corvane</div>
    <div class="website">www.corvane-hvac.com</div>
  </section>

  <section class="card card--back" aria-label="Card back">
    <div class="brand-name">corvane</div>
    <div class="person">
      <div class="person-name">Walter Brinoku</div>
      <div class="person-title">Home comfort consultant</div>
    </div>
    <div class="rule"></div>
    <svg class="address-band" viewBox="0 0 448 32" aria-hidden="true">
      <polygon points="0,0 448,0 448,32 18,32" fill="var(--band)"/>
    </svg>
    <div class="address-text">4827 Dunmore St #215 Oakland, CA 94619</div>
    <ul class="contacts">
      <li class="contact">
        <svg viewBox="0 0 24 24" aria-hidden="true"><path d="M2 8c0-3 5-5 10-5s10 2 10 5v2h-5V8H7v2H2z"/><path d="M5 12h14l2 9H3z M12 14a3 3 0 1 0 0 6a3 3 0 1 0 0-6z"/></svg>
        <span>888-316-2790</span>
      </li>
      <li class="contact">
        <svg viewBox="0 0 24 24" aria-hidden="true"><path d="M6.6 10.8a15 15 0 0 0 6.6 6.6l2.2-2.2a1 1 0 0 1 1-.25 11.4 11.4 0 0 0 3.6.57 1 1 0 0 1 1 1V20a1 1 0 0 1-1 1A17 17 0 0 1 3 4a1 1 0 0 1 1-1h3.5a1 1 0 0 1 1 1 11.4 11.4 0 0 0 .57 3.6 1 1 0 0 1-.25 1z"/></svg>
        <span>510-742-3185</span>
      </li>
      <li class="contact">
        <svg viewBox="0 0 24 24" aria-hidden="true"><path d="M3 6h18v12H3z M4 7l8 6 8-6" fill="none" stroke="var(--ink-soft)" stroke-width="1.8"/></svg>
        <span>walter@corvane-hvac.com</span>
      </li>
    </ul>
    <div class="license">Lic.# 584261</div>
  </section>

</main>
</body>
</html>
```